American cannabis tech company business card design

Pavrel.com is seeking a modern, professional, and brand-aligned business card that represents our company and its core values: Mission, Story, Values, and Impact. As an innovative cannabis company, we want a business card that is not only visually appealing but also serves as a representation of who we are and what we stand for.

Project Scope: Design a double-sided business card that integrates our brand identity and core values. Incorporate our key brand elements, ensuring a sleek and contemporary aesthetic. Visually reflect our core values (Mission, Story, Values, Impact) in a way that is engaging yet professional.

Target Market(s)

Vendors, third parties,

Contact Information for Business Card

Contact details (name, title, email, phone, website, etc.)

Font styles to use
Other font styles liked:
• Caslon, Centra

Colors

Designer to choose colors to be used in the design.

Requirements
Must have
• Pavrel.com logo and branding A creative yet clean way to integrate our core values (Mission, Story, Values, Impact) Modern typography and a well-structured layout
Nice to have
• forest green, grey, white, black
Should not have
• references to marijuana, leafs, plants, or related product

```html
<!DOCTYPE html>
<html lang="en">
<head>
<meta charset="utf-8">
<title>Pavrel.com Business Card</title>
<link href="https://fonts.googleapis.com/css2?family=Playfair+Display:wght@700;900&family=Montserrat:wght@400;500&display=swap" rel="stylesheet">
<style>
  :root {
    --backdrop: #2a2b2d;
    --forest: #1f3d22;
    --forest-deep: #193219;
    --strip: #26422a;
    --strip-mark: #173019;
    --cream: #f4f1e8;
    --paper: #ffffff;
    --ink: #1c1c1c;
    --ink-green: #1f3d22;
  }
  * { box-sizing: border-box; margin: 0; padding: 0; }
  html, body { width: 1200px; height: 900px; overflow: hidden; }
  body {
    background: var(--backdrop);
    display: flex;
    flex-direction: column;
    align-items: center;
    justify-content: center;
    gap: 40px;
  }
  .card {
    width: 680px;
    height: 388px;
    border-radius: 26px;
    overflow: hidden;
    position: relative;
    box-shadow: 0 10px 30px rgba(0,0,0,0.35);
  }
  .card-front {
    background: linear-gradient(135deg, var(--forest) 0%, var(--forest-deep) 100%);
    display: flex;
    align-items: center;
    justify-content: center;
  }
  .wordmark {
    font-family: "Playfair Display", serif;
    font-weight: 900;
    color: var(--cream);
    font-size: 118px;
    letter-spacing: 2px;
    line-height: 1;
  }
  .card-back {
    background: var(--paper);
    display: flex;
  }
  .back-content {
    flex: 1;
    padding: 46px 40px 40px 46px;
    display: flex;
    flex-direction: column;
    justify-content: space-between;
  }
  .person-name {
    font-family: "Playfair Display", serif;
    font-weight: 700;
    font-size: 26px;
    color: var(--ink-green);
    line-height: 1.1;
  }
  .person-title {
    font-family: "Playfair Display", serif;
    font-weight: 700;
    font-size: 13px;
    color: var(--ink);
    margin-left: 14px;
    margin-top: 2px;
  }
  .contact {
    font-family: "Montserrat", sans-serif;
    font-size: 15px;
    color: var(--ink);
    line-height: 1.3;
  }
  .address { margin-bottom: 16px; }
  .contact-list { list-style: none; }
  .contact-list li {
    display: flex;
    align-items: center;
    gap: 10px;
    margin-top: 4px;
  }
  .contact-list svg { width: 14px; height: 14px; flex: none; }
  .brand-strip {
    width: 150px;
    background: var(--strip);
    position: relative;
  }
  .strip-mark {
    position: absolute;
    left: 50%;
    top: 50%;
    transform: translate(-50%, -50%) rotate(90deg);
    font-family: "Playfair Display", serif;
    font-weight: 900;
    font-size: 82px;
    color: var(--strip-mark);
    white-space: nowrap;
    line-height: 1;
  }
</style>
</head>
<body>
  <section class="card card-front">
    <span class="wordmark">PAVREL</span>
  </section>

  <section class="card card-back">
    <div class="back-content">
      <div class="identity">
        <p class="person-name">Dana Whitfield</p>
        <p class="person-title">Owner</p>
      </div>
      <div class="contact">
        <p class="address">415 Harlow Ave, #112<br>Brookfield, OH 43015</p>
        <ul class="contact-list">
          <li>
            <svg viewBox="0 0 16 16" aria-hidden="true"><path fill="#1f3d22" d="M3.6 1.2l2.3 2.6-1.3 1.7c.9 2 2.4 3.6 4.4 4.5l1.7-1.3 2.6 2.3-1.4 2.4C6.7 13.1 2.9 9.3 1.2 4.1z"/></svg>
            614-555-0142
          </li>
          <li>
            <svg viewBox="0 0 16 16" aria-hidden="true"><rect x="1" y="3" width="14" height="10" rx="1" fill="#1f3d22"/><path d="M1.5 3.8L8 8.6l6.5-4.8" stroke="#fff" stroke-width="1.2" fill="none"/></svg>
            info@pavrel.com
          </li>
          <li>
            <svg viewBox="0 0 16 16" aria-hidden="true"><circle cx="8" cy="8" r="7" fill="#1f3d22"/><path d="M1 8h14M8 1c2.5 2.5 2.5 11.5 0 14M8 1c-2.5 2.5-2.5 11.5 0 14" stroke="#fff" stroke-width="1" fill="none"/></svg>
            www.pavrel.com
          </li>
        </ul>
      </div>
    </div>
    <div class="brand-strip">
      <span class="strip-mark">PAVREL</span>
    </div>
  </section>
</body>
</html>
```